Marwick Law Letterhead

We need a new letterhead design for a Law Firm. The address for the law firm is 1475 Calloway Street, Suite 210, Houston, Texas 77041. Phone Number: 832-361-9027; Fax Number: 832-614-7359. The logo is uploaded to the project.

```html
<!DOCTYPE html>
<html lang="en">
<head>
<meta charset="utf-8">
<title>Marwick Law Letterhead</title>
<link rel="stylesheet" href="https://fonts.googleapis.com/css2?family=Montserrat:wght@400;500;600&display=swap">
<style>
  :root {
    --navy: #1b2f5e;
    --red: #8b0e14;
    --red-bright: #c8141c;
    --ink: #232323;
    --paper: #ffffff;
    --backdrop: #e8e8e8;
    --signature: #d6d6d6;
  }
  * { box-sizing: border-box; margin: 0; padding: 0; }
  html, body {
    width: 1154px;
    height: 1200px;
    overflow: hidden;
    background: var(--backdrop);
    font-family: "Montserrat", sans-serif;
    color: var(--ink);
  }
  .letterhead {
    position: absolute;
    left: 161px;
    top: 19px;
    width: 831px;
    height: 1162px;
    background: var(--paper);
    overflow: hidden;
  }
  .brand {
    position: absolute;
    left: 28px;
    top: 78px;
    display: flex;
    align-items: center;
    gap: 12px;
  }
  .brand-square {
    width: 26px;
    height: 26px;
    background: var(--navy);
  }
  .brand-name {
    font-size: 28px;
    font-weight: 600;
    color: var(--navy);
    letter-spacing: 0.5px;
  }
  .contact {
    position: absolute;
    left: 622px;
    top: 63px;
    height: 98px;
    padding-left: 13px;
    border-left: 1.5px solid var(--red);
    font-size: 13.6px;
    line-height: 18px;
  }
  .contact-address { margin-bottom: 11px; margin-top: -2px; }
  .contact-line {
    display: flex;
    align-items: center;
    gap: 9px;
    line-height: 20.5px;
  }
  .contact-line svg { width: 13px; height: 13px; flex: none; }
  .recipient {
    position: absolute;
    left: 31px;
    top: 268px;
    font-size: 13.3px;
    line-height: 20.6px;
  }
  .letter-body {
    position: absolute;
    left: 33px;
    top: 355px;
    width: 769px;
    font-size: 13.3px;
    line-height: 20.7px;
    text-align: justify;
    hyphens: auto;
  }
  .letter-body p + p { margin-top: 20.7px; }
  .closing {
    position: absolute;
    left: 30px;
    top: 936px;
    font-size: 17px;
  }
  .signature {
    position: absolute;
    left: 28px;
    top: 966px;
    width: 94px;
    height: 31px;
    background: var(--signature);
    border-radius: 3px;
  }
  .footer-band {
    position: absolute;
    left: 0;
    bottom: 0;
    width: 831px;
    height: 116px;
    display: block;
  }
</style>
</head>
<body>
  <main class="letterhead">
    <header>
      <div class="brand">
        <span class="brand-square"></span>
        <span class="brand-name">Marwick Law</span>
      </div>
      <address class="contact" style="font-style: normal;">
        <div class="contact-address">1475 Calloway Street,<br>Suite 210, Houston,<br>Texas 77041</div>
        <div class="contact-line">
          <svg viewBox="0 0 24 24" aria-hidden="true"><path fill="var(--red-bright)" d="M6.6 10.8a15.1 15.1 0 0 0 6.6 6.6l2.2-2.2a1 1 0 0 1 1-.25 11.4 11.4 0 0 0 3.6.57 1 1 0 0 1 1 1V20a1 1 0 0 1-1 1A17 17 0 0 1 3 4a1 1 0 0 1 1-1h3.5a1 1 0 0 1 1 1c0 1.25.2 2.45.57 3.57a1 1 0 0 1-.25 1z"/></svg>
          <span>832-361-9027</span>
        </div>
        <div class="contact-line">
          <svg viewBox="0 0 24 24" aria-hidden="true"><path fill="var(--red-bright)" d="M7 3h10v5H7zM4 9h16a2 2 0 0 1 2 2v6h-4v4H6v-4H2v-6a2 2 0 0 1 2-2zm4 7v3h8v-3z"/></svg>
          <span>832-614-7359</span>
        </div>
      </address>
    </header>

    <section class="recipient">
      Mr/s<br>First Name and Last Name<br>Company Name<br>Address
    </section>

    <section class="letter-body" lang="la">
      <p>Lorem ipsum dolor sit amet,consectetur adipiscing sed do eiusmod tempor incididunt laboreet dolore magna aliqua.Ut enim ad minim.veniam, quis nostrud exercitation ullamco laboris nisi ut aliquip exea commodo consequat.Lorem ipsum dolor sit amet,consectetur adipiscing sed do eiusmod tempor incididunt.labore et dolore magna aliqua. Ut enim</p>
      <p>Lorem ipsum dolor sit amet, consectetur adipiscing sed do eiusmod tempor incididunt labore et dolore magna aliqua. Ut enim ad minim veniam, quis nostrud exercitation ullamco laboris nisi ut aliquip exea commodo consequat.Duis aute irure dolor in reprehenderit in voluptate velit esse cillum irure dolor in reprehenderit in voluptate velit esse irure</p>
      <p>Lorem ipsum dolor sit amet, consectetur adipiscing sed do eiusmod tempor incididunt labore et dolore magna aliqua. consequat. Duis aute irure dolor in.reprehenderit in voluptate velit esse cillum dolore eu fugiat nulla pariatur. Excepteur sint occaecat cupidatat non proident, sunt in culpa qui officia deserunt mollit,</p>
      <p>Lorem ipsum dolor sit amet, consectetur adipiscing sed do eiusmod tempor incididunt labore et dolore magna aliqua. Ut enim Lorem ipsum dolor sit amet, consectetur adipiscing sed do eiusmod tempor incididunt labore et dolore magna aliqua. Ut enim Lorem ipsum aliqua.ipsum</p>
      <p>Lorem ipsum dolor sit amet, consectetur adipiscing sed do eiusmod tempor incididunt labore et dolore magna aliqua. Ut enim ad minim veniam, quis nostrud exercitation ullamco laboris nisi ut aliquip exea commodo consequat.Duis aute irure dolor in reprehenderit in voluptate velit esse cillum irure dolor in reprehenderit in voluptate velit esse irure</p>
      <p>Lorem ipsum dolor sit amet, consectetur adipiscing sed do eiusmod tempor incididunt labore et dolore magna aliqua. Ut enim ad minim veniam, quis nostrud exercitation ullamco laboris nisi ut aliquip exea commodo consequat.Duis aute irure dolor in reprehenderit in voluptate velit esse cillum irure dolor in reprehenderit in voluptate velit esse irure</p>
    </section>

    <p class="closing">Regards</p>
    <div class="signature" role="img" aria-label="Handwritten signature of the sender"></div>

    <svg class="footer-band" viewBox="0 0 831 116" preserveAspectRatio="none" aria-hidden="true">
      <path fill="var(--red)" d="M0 37 Q415.5 -37 831 37 V116 H0 Z"/>
      <path fill="var(--navy)" d="M0 44 Q415.5 -28 831 44 V116 H0 Z"/>
    </svg>
  </main>
</body>
</html>
```